Need a website to promote and sell my book

Using images from the book, I need a website designed that helps promote the book and eventually sell it.
*Need a landing page
*About the author page
*Storefront page to purchase
*Coming soon page
*"Featured in" page that can link to news articles etc.
The images posted here are examples, the winner of the contest will get the images from the finished book. I will provide the exact text to the winner of the contest.

I can also provide images of kids reading the book. For now, I'll just use one, the winner can have them all to choose from.
Updates

Extending deadline to allow for a few more designers to submit and to allow time for me to review and hold a poll

Target Market(s)

Parents, aunts, uncles, grandparents, friends who have kids; teachers, daycare teachers, babysitters etc.

Industry/Entity Type

Custom Publishing

Coding

Coded - Design and coding required

Number of Pages Required

5+ page

Font styles to use
Sans Serif

Colors

Designer to choose colors to be used in the design.

Requirements
Must have
• It must have a fun feel like the book.
Nice to have
• Would be great to have a section that automatically pulls tweets about the book into it.

```html
<!DOCTYPE html>
<html lang="en">
<head>
<meta charset="utf-8">
<title>Maren Holloway — About the Author</title>
<link href="https://fonts.googleapis.com/css2?family=Gochi+Hand&family=Patrick+Hand&display=swap" rel="stylesheet">
<style>
:root{
  --sky:#7bd0e8;
  --sky-deep:#5fb9d6;
  --orange-top:#fcc078;
  --orange-bottom:#eea64d;
  --orange-line:#e08a12;
  --orange-soft:#f5b561;
  --coral:#ef6469;
  --coral-text:#f0545b;
  --paper:#f5f5f5;
  --ink:#2e2e2e;
  --muted:#777;
  --white:#fff;
  --star:#f7b515;
}
*{margin:0;padding:0;box-sizing:border-box}
html,body{width:1200px;height:2378px;overflow:hidden}
body{position:relative;font-family:"Patrick Hand",cursive;color:var(--ink);background:var(--white)}
.abs{position:absolute}
.hero{left:0;top:0;width:1200px;height:430px;background:var(--sky)}
.deco{background:var(--sky-deep);opacity:.55;border-radius:18px}
.wordmark{display:flex;align-items:center;gap:12px;font-family:"Patrick Hand",cursive;color:var(--coral-text);white-space:nowrap}
.wordmark i{display:block;border-radius:50%;background:var(--coral-text)}
.brand{left:175px;top:120px;font-size:44px}
.brand i{width:26px;height:26px}
.nav{top:50px;left:533px;display:flex;gap:30px;font-size:17px;color:var(--white)}
.btn-buy{left:968px;top:42px;width:110px;height:43px;border-radius:10px;background:var(--white);color:var(--sky-deep);font-size:17px;display:flex;align-items:center;justify-content:center}
.portrait{left:170px;top:293px;width:274px;height:273px;border:5px solid var(--orange-line);border-radius:46% 44% 48% 42%;background:linear-gradient(160deg,#c99a6e,#7b5a44 60%,#3a3230);z-index:2}
.kicker{left:545px;top:318px;color:var(--coral-text);font-size:22px}
.name{left:543px;top:348px;color:var(--white);font-family:"Gochi Hand",cursive;font-weight:400;font-size:54px}
.social-top{left:990px;top:370px;display:flex;gap:12px;color:var(--white);font-size:16px}
.about{left:0;top:430px;width:1200px;height:720px;z-index:1}
.facts{font-size:18px;color:var(--white);z-index:2}
.divider{left:798px;top:463px;width:1px;height:78px;background:rgba(255,255,255,.6);z-index:2}
.side{left:182px;top:593px;width:253px;z-index:2}
.side li{list-style:none;height:42px;line-height:42px;padding-left:31px;font-size:18px;color:var(--white)}
.side li.active{background:var(--orange-soft);border-left:5px solid var(--orange-line);padding-left:26px}
.bio{left:545px;top:584px;width:535px;font-size:19px;line-height:30.4px;color:var(--white);z-index:2}
.books{left:0;top:1060px;width:1200px;height:565px;background:var(--paper)}
.books-title{left:168px;top:1175px;font-family:"Gochi Hand",cursive;font-weight:400;font-size:36px;color:var(--ink)}
.book{width:193px;text-align:center;top:1286px}
.cover{width:193px;height:192px;background:#aeaeae}
.cover.main{background:linear-gradient(180deg,#6fc6e4 0%,#8fd2ea 55%,#f3c47e 100%)}
.book p{margin-top:8px;font-size:16px;line-height:18px}
.stars{color:var(--star);font-size:16px;letter-spacing:4px;margin-top:4px}
.contact h3,.sub h3{font-weight:400;font-size:18px;color:var(--coral-text)}
.contact{font-size:16px;color:var(--muted)}
.row{display:flex;gap:14px;align-items:flex-start;margin-top:12px}
.row svg{flex:none;margin-top:3px}
.press{left:0;top:1905px;width:1200px;height:170px}
.press-names{left:120px;top:1978px;width:960px;display:flex;justify-content:space-between;font-size:30px;color:#f6a3a6}
.kid{left:0;top:2040px;width:175px;height:280px;border-radius:45% 50% 30% 30%;background:linear-gradient(180deg,#c98a4e,#e8c09c 40%,#8f8f9e);z-index:3}
.sub{left:270px;top:2140px}
.field{left:240px;top:2180px;width:351px;height:40px;border:2px solid var(--coral);border-radius:22px}
.field span{position:absolute;left:28px;top:8px;font-size:15px;color:var(--muted)}
.field b{position:absolute;right:3px;top:3px;width:100px;height:30px;border-radius:16px;background:var(--coral);color:var(--white);font-weight:400;font-size:13px;display:flex;align-items:center;justify-content:center}
.social-label{left:270px;top:2240px;font-size:17px;color:var(--coral-text)}
.social-foot{left:455px;top:2241px;display:flex;gap:14px;font-size:16px;color:var(--muted)}
.foot-links{left:703px;top:2142px;font-size:16px;color:var(--muted);line-height:30.5px;list-style:none}
.foot-brand{left:890px;top:2180px;font-size:30px}
.foot-brand i{width:18px;height:18px}
.legal{left:0;top:2348px;width:1200px;height:30px;background:#ededed;text-align:center;font-size:13px;line-height:30px;color:var(--ink)}
</style>
</head>
<body>

<header class="abs hero">
  <div class="abs deco" style="left:40px;top:108px;width:92px;height:90px" role="img" aria-label="Lab stand doodle"></div>
  <div class="abs deco" style="left:560px;top:110px;width:120px;height:190px" role="img" aria-label="Microscope illustration"></div>
  <div class="abs deco" style="left:760px;top:138px;width:105px;height:125px" role="img" aria-label="Test tubes doodle"></div>
  <div class="abs deco" style="left:1035px;top:105px;width:80px;height:85px;border-radius:50%" role="img" aria-label="Atom doodle"></div>
  <div class="abs deco" style="left:920px;top:200px;width:120px;height:130px" role="img" aria-label="Flask illustration"></div>
  <div class="abs deco" style="left:1110px;top:255px;width:90px;height:125px;border-radius:40px" role="img" aria-label="Molecule illustration"></div>
  <div class="abs deco" style="left:460px;top:300px;width:80px;height:90px" role="img" aria-label="Syringe doodle"></div>
  <div class="abs deco" style="left:350px;top:282px;width:80px;height:55px;border-radius:40px" role="img" aria-label="Ball illustration"></div>
  <div class="abs deco" style="left:0;top:370px;width:48px;height:60px;border-radius:24px" role="img" aria-label="Doodle"></div>

  <div class="abs wordmark brand"><i></i><span>Play with Science</span></div>

  <nav class="abs nav"><span>About Book</span><span>About author</span><span>Featured In</span><span>Contact</span></nav>
  <div class="abs btn-buy">Purchase</div>

  <p class="abs kicker">A little bit about,</p>
  <h1 class="abs name">Maren Holloway</h1>
  <div class="abs social-top"><span>Pals</span><span>Buzz</span><span>Links</span></div>
</header>

<section class="abs books"></section>

<div class="abs portrait" role="img" aria-label="Portrait photo of the author outdoors in tall grass"></div>

<section class="abs about">
  <svg width="1200" height="720" viewBox="0 0 1200 720" style="position:absolute;left:0;top:0">
    <defs><linearGradient id="og" x1="0" y1="0" x2="0" y2="1"><stop offset="0" stop-color="#fcc078"/><stop offset="1" stop-color="#eea64d"/></linearGradient></defs>
    <path d="M0 0H1200V673C1100 690 980 700 880 700C700 700 480 640 300 640C170 640 70 652 0 657Z" fill="url(#og)"/>
    <path d="M1200 673C1100 690 980 700 880 700C700 700 480 640 300 640C170 640 70 652 0 657" fill="none" stroke="#e08a12" stroke-width="2"/>
  </svg>
</section>

<div class="abs facts" style="left:545px;top:468px">Author / Lecturer</div>
<div class="abs facts" style="left:545px;top:510px">PhD in Sociology</div>
<div class="abs divider"></div>
<div class="abs facts" style="left:866px;top:468px">Volunteer at Little Tower Club</div>
<div class="abs facts" style="left:866px;top:510px">Live in Brookvale, CA, USA</div>

<ul class="abs side">
  <li class="active">About Maren</li><li>Press</li><li>Appearances</li><li>Maren's Books</li><li>Awards and Nominations</li>
</ul>

<p class="abs bio">Lorem ipsum dolor sit amet, consectetur adipiscing elit. Cras non enim congue, luctus nibh eget, egestas risus. Nunc quis convallis mi. Suspendisse sit amet dolor non lectus feugiat sollicitudin. Proin pretium mauris vel felis sollicitudin pretium. Vestibulum ornare congue est, in ullamcorper nisi fringilla vitae. Fusce a urna id ante pretium bibendum. Quisque quis mi diam. Fusce vitae diam et est consectetur pretium. Maecenas iaculis at risus vel malesuada. Integer mollis erat in erat pretium, nec laoreet tortor malesuada. Maecenas ligula quam, condimentum maximus mi hendrerit, tincidunt suscipit tellus. Nullam consectetur, purus egestas facilisis euismod, ex dolor dignissim ex, non molestie sapien ex ut magna. Lorem ipsum dolor sit amet, consectetur adipiscing elit. Sed ligula magna, commodo ac tellus in, fringilla vestibulum nunc. Proin aliquet, libero sit amet tempus interdum, lacus neque dapibus elit, ut blandit dui sem in velit. Donec ipsum erat, viverra ac vestibulum at, vulputate eu nunc.</p>

<h2 class="abs books-title">Maren's books</h2>

<div class="abs book" style="left:121px"><div class="cover main" role="img" aria-label="Book cover with children reading among science doodles"></div><p>Play with<br>Science</p><div class="stars">★★★★★</div></div>
<div class="abs book" style="left:377px"><div class="cover" role="img" aria-label="Book cover placeholder"></div><p>Sample book 02</p><div class="stars">★★★★★</div></div>
<div class="abs book" style="left:634px"><div class="cover" role="img" aria-label="Book cover placeholder"></div><p>Sample book 03</p><div class="stars">★★★★★</div></div>
<div class="abs book" style="left:885px"><div class="cover" role="img" aria-label="Book cover placeholder"></div><p>Sample book 04</p><div class="stars">★★★★★</div></div>

<div class="abs contact" style="left:170px;top:1683px">
  <h3>Send all your thoughts;</h3>
  <div class="row" style="margin-top:18px"><svg width="14" height="14" viewBox="0 0 24 24"><path d="M6.6 10.8a15 15 0 0 0 6.6 6.6l2.2-2.2a1 1 0 0 1 1-.25 11 11 0 0 0 3.6.6 1 1 0 0 1 1 1V20a1 1 0 0 1-1 1A17 17 0 0 1 3 4a1 1 0 0 1 1-1h3.5a1 1 0 0 1 1 1 11 11 0 0 0 .6 3.6 1 1 0 0 1-.25 1z" fill="#888"/></svg><span>555-014-2290</span></div>
  <div class="row"><svg width="14" height="12" viewBox="0 0 24 18"><rect width="24" height="18" rx="2" fill="#888"/><path d="M1 2l11 8 11-8" stroke="#fff" stroke-width="2" fill="none"/></svg><span>hello@hollowaylearning.com</span></div>
  <div class="row"><svg width="12" height="16" viewBox="0 0 12 16"><path d="M6 0a6 6 0 0 1 6 6c0 4.5-6 10-6 10S0 10.5 0 6a6 6 0 0 1 6-6z" fill="#888"/><circle cx="6" cy="6" r="2.2" fill="#fff"/></svg><span style="line-height:19px">412 Maple Grove Rd,<br>Fairview,<br>CA 90000,<br>USA.</span></div>
</div>

<div class="abs contact" style="left:635px;top:1683px;width:400px">
  <h3>For Inquiries</h3>
  <p style="margin-top:18px;line-height:21px">Lorem ipsum dolor sit amet, consectetur adipiscing elit. Cras non enim congue, luctus nibh eget, egestas risus. Nunc quis convallis mi.</p>
  <p style="margin-top:20px;color:var(--coral-text)">contact@hollowaylearning.com</p>
</div>

<svg class="abs press" viewBox="0 0 1200 170" width="1200" height="170">
  <defs><pattern id="zig" width="20" height="10" patternUnits="userSpaceOnUse"><path d="M0 0H20L10 6Z" fill="#ef6469"/></pattern></defs>
  <path d="M0 30C300 10 700 0 1200 28V160H0Z" fill="#ef6469"/>
  <rect x="0" y="160" width="1200" height="8" fill="url(#zig)"/>
</svg>
<div class="abs press-names"><span>Pagewell</span><span>Readers Daily</span><span>Inkline</span><span>Folio</span><span>Shelfnote</span></div>

<div class="abs kid" role="img" aria-label="Illustrated child hugging a toy elephant"></div>

<div class="abs sub"><h3>Subscribe us for latest news.!</h3></div>
<div class="abs field"><span>your email</span><b>Subscribe</b></div>
<div class="abs social-label">We're on social :</div>
<div class="abs social-foot"><span>Pals</span><span>Buzz</span><span>Links</span><span>Clips</span></div>

<ul class="abs foot-links"><li>About author</li><li>Featured In</li><li>Purchase</li><li>Contact</li></ul>
<div class="abs wordmark foot-brand"><i></i><span>Play with Science</span></div>

<footer class="abs legal">©2020 www.playwithscience.com All rights reserved.</footer>

</body>
</html>
```